Web Design Project for SEARCH ENGINE !

We need a website design for torrents search engine.

The Website will be www.Qentrova.com

Qentrova is a a search engine for torrents.
Qentrova search and index torrents results from all torrents sites.

We will need:
Logo
WebSite Design
slogen (optional)

we need only PSDs - no codded pages are needed !

Design to the following screen Size & resolution: 1024 x 768

***PLEASE DOWNLOAD ATTACHED FILE !

```html
<!DOCTYPE html>
<html lang="en">
<head>
<meta charset="utf-8">
<title>Qentrova – Torrent Search</title>
<link rel="stylesheet" href="https://fonts.googleapis.com/css2?family=Arimo:wght@400;700&family=Open+Sans:wght@400;700&display=swap">
<style>
  :root {
    --page-bg: #f7f7f7;
    --column-bg: #ffffff;
    --ink: #111111;
    --accent: #e0530a;
    --accent-dark: #c74400;
    --band: #efefef;
    --nav-bg: #111111;
    --footer-bg: #6b6b6b;
    --footer-ink: #2f2f2f;
    --footer-rule: #8a8a8a;
    --bar-top: #f4f4f6;
    --bar-bottom: #a9a9ae;
    --field: #e4e4e6;
    --social-blue: #3b5a9a;
    --social-sky: #3fa9e0;
    --social-orange: #f18a1c;
  }
  * { box-sizing: border-box; }
  html, body {
    margin: 0; width: 1200px; height: 900px; overflow: hidden;
    background: var(--page-bg);
    font-family: "Arimo", Arial, sans-serif;
    color: var(--ink);
  }
  .page {
    position: absolute; left: 26px; top: 0; width: 1148px; height: 900px;
    background: var(--column-bg);
    box-shadow: 0 0 8px rgba(0,0,0,.45);
  }
  .brand {
    position: absolute; left: 40px; top: 16px; height: 110px;
    display: flex; align-items: center; gap: 12px;
  }
  .brand-mark {
    width: 112px; height: 112px; border-radius: 50%;
    background: var(--accent);
  }
  .brand-name {
    font-size: 52px; font-weight: 700; color: var(--ink); letter-spacing: 1px;
  }
  .main-nav {
    position: absolute; left: 777px; top: 43px; width: 383px; height: 50px;
    background: var(--nav-bg); border-radius: 8px 8px 0 8px;
    display: flex; justify-content: space-around; align-items: center;
    padding: 0 14px;
  }
  .main-nav a {
    color: #fff; text-decoration: none; font-size: 15px;
  }
  .social {
    position: absolute; left: 991px; top: 102px; display: flex; gap: 8px;
  }
  .social span {
    width: 39px; height: 39px; border-radius: 7px; display: block;
  }
  .social .s1 { background: var(--social-blue); }
  .social .s2 { background: var(--social-sky); }
  .social .s3 { background: var(--social-orange); }
  .rule {
    position: absolute; left: 19px; top: 150px; width: 1112px; height: 2px;
    background: var(--accent);
  }
  .search-bar {
    position: absolute; left: 23px; top: 152px; width: 1102px; height: 57px;
    background: linear-gradient(var(--bar-top), #dedee2 60%, var(--bar-bottom));
    border-radius: 0 0 6px 6px;
  }
  .search-field {
    position: absolute; left: 30px; top: 16px; width: 855px; height: 28px;
    background: var(--field); border: 2px solid #a8a8a8;
    border-right-color: #d6d6d6; border-bottom-color: #d6d6d6;
    font-size: 15px; padding: 4px 0 0 22px; color: var(--ink);
  }
  .search-button {
    position: absolute; left: 942px; top: 16px; width: 130px; height: 28px;
    background: linear-gradient(#f06a1a, var(--accent-dark));
    color: #fff; font-size: 15px; text-align: center; line-height: 28px;
  }
  .intro {
    position: absolute; left: 0; top: 255px; width: 1148px; height: 390px;
    background: var(--band); text-align: center; font-size: 14px;
  }
  .intro p { position: absolute; left: 0; right: 0; margin: 0; }
  .intro a { color: var(--accent); text-decoration: none; }
  .actions {
    position: absolute; left: 0; right: 0; top: 120px;
    display: flex; justify-content: center; gap: 12px; align-items: center;
  }
  .plus-badge { width: 82px; height: 28px; background: #dcdcdc; border: 1px solid #c4c4c4; border-radius: 3px; }
  .signin {
    height: 27px; padding: 0 10px 0 8px; background: #4a66a6; border-radius: 3px;
    color: #fff; font-size: 13px; font-weight: 700; display: flex; align-items: center; gap: 8px;
  }
  .signin i { width: 14px; height: 14px; background: #fff; opacity: .85; display: block; border-radius: 2px; }
  .site-footer {
    position: absolute; left: 0; top: 789px; width: 1148px; height: 111px;
    background: var(--footer-bg); font-family: "Open Sans", Verdana, sans-serif;
    color: var(--footer-ink); font-size: 13px;
  }
  .footer-copy { position: absolute; left: 328px; top: 49px; }
  .footer-divider { position: absolute; left: 445px; top: 40px; width: 1px; height: 45px; background: var(--footer-rule); }
  .footer-links { position: absolute; left: 465px; top: 36px; line-height: 22px; }
  .footer-links a { color: var(--footer-ink); text-decoration: none; }
  .footer-links .sep { color: var(--footer-rule); margin: 0 6px; }
  .footer-links strong { font-weight: 700; }
</style>
</head>
<body>
<div class="page">
  <header>
    <div class="brand">
      <span class="brand-mark"></span>
      <span class="brand-name">Qentrova</span>
    </div>
    <nav class="main-nav">
      <a href="#">Search</a><a href="#">Qentrova</a><a href="#">Profile</a><a href="#">Help</a>
    </nav>
    <div class="social"><span class="s1"></span><span class="s2"></span><span class="s3"></span></div>
    <div class="rule"></div>
    <div class="search-bar">
      <div class="search-field">Type URL Here</div>
      <div class="search-button">Search</div>
    </div>
  </header>

  <main class="intro">
    <p style="top:78px">Qentrova Lorem ipsum dolor sit amet, consectetuer adipiscing elit. Aenean commodo ligula eget <a href="#">dolor</a>.</p>
    <div class="actions">
      <span class="plus-badge"></span>
      <span class="signin"><i></i>Sign in with Linkbase</span>
    </div>
    <p style="top:168px">Indexing 15.337.488 active Qentrova from 60.307.316 pages on 33 domains</p>
    <p style="top:212px">find the best <a href="#">online games</a></p>
    <p style="top:263px"><a href="#">SSL</a> | <a href="#">Qentrova plugin</a> | <a href="#">Borwser search plugin</a></p>
    <p style="top:298px">©2011 : Qentrova</p>
  </main>

  <footer class="site-footer">
    <div class="footer-copy">© 2011 Qentrova</div>
    <div class="footer-divider"></div>
    <div class="footer-links">
      <a href="#"><strong>change language</strong></a><span class="sep">|</span><a href="#">lite</a><span class="sep">|</span><a href="#">achievements</a><span class="sep">|</span><a href="#">latest searches</a><span class="sep">|</span><a href="#">api</a><span class="sep">|</span><a href="#">chat</a><span class="sep">|</span><br>
      <a href="#">about</a><span class="sep">|</span><a href="#">privacy</a><span class="sep">|</span><a href="#">dmca</a><span class="sep">|</span><a href="#">rules</a><span class="sep">|</span><a href="#">stats</a><span class="sep">|</span><a href="#">logos</a><span class="sep">|</span><a href="#">contacts</a>
    </div>
  </footer>
</div>
</body>
</html>
```